Corvane Capital Business Cards

These are professional business cards that are for my family office.
Put fake emails and phone numbers as of now until I finalize those components. This family office controls my families investments, assets, and future. The cards should be professional.
..
.
.
.
I just uploaded another variation of a logo I would like to see as a business card to I am inbeteen which logo to use

Target Market(s)

business

Industry/Entity Type

business

Contact Information for Business Card

Professional, wealth related, finance related.

Requirements
Must have
• Logo

```html
<!DOCTYPE html>
<html lang="en">
<head>
<meta charset="utf-8">
<title>Corvane Capital Business Cards</title>
<link href="https://fonts.googleapis.com/css2?family=Cinzel:wght@400;600&family=Montserrat:wght@400;700&display=swap" rel="stylesheet">
<style>
  :root {
    --backdrop: #e4e4e4;
    --card: #050505;
    --ink: #ffffff;
    --ink-soft: #d6d6d6;
    --rule: #bdbdbd;
    --shadow: rgba(0, 0, 0, 0.35);
  }
  * { box-sizing: border-box; margin: 0; padding: 0; }
  html, body {
    width: 1200px;
    height: 813px;
    overflow: hidden;
    background: var(--backdrop);
  }
  .sheet {
    position: relative;
    width: 1200px;
    height: 813px;
  }
  .card {
    position: absolute;
    width: 560px;
    height: 320px;
    background: var(--card);
    border-radius: 4px;
    box-shadow: 0 14px 30px var(--shadow);
    color: var(--ink);
  }
  .card--front { left: 70px; top: 90px; }
  .card--back { left: 570px; top: 400px; }

  .brand {
    display: flex;
    align-items: center;
    gap: 18px;
  }
  .brand__circle {
    width: 84px;
    height: 84px;
    border: 3px solid var(--ink);
    border-radius: 50%;
    flex: none;
  }
  .brand__name {
    font-family: "Cinzel", serif;
    font-weight: 400;
    color: var(--ink);
    white-space: nowrap;
  }

  .card--front .brand {
    position: absolute;
    inset: 0;
    justify-content: center;
  }
  .card--front .brand__name { font-size: 34px; }

  .card--back .brand {
    position: absolute;
    left: 36px;
    top: 0;
    height: 100%;
    flex-direction: column;
    justify-content: center;
    gap: 12px;
    width: 200px;
  }
  .card--back .brand__circle { width: 110px; height: 110px; }
  .card--back .brand__name { font-size: 15px; }

  .divider {
    position: absolute;
    left: 262px;
    top: 78px;
    width: 1.5px;
    height: 170px;
    background: var(--rule);
  }
  .details {
    position: absolute;
    left: 290px;
    top: 70px;
  }
  .details__company {
    font-family: "Cinzel", serif;
    font-size: 21px;
    letter-spacing: 0.5px;
    margin-bottom: 22px;
  }
  .details__name {
    font-family: "Montserrat", sans-serif;
    font-weight: 700;
    font-size: 20px;
    letter-spacing: 0.5px;
  }
  .details__role {
    font-family: "Montserrat", sans-serif;
    font-size: 14px;
    color: var(--ink-soft);
    margin-bottom: 16px;
  }
  .contact {
    list-style: none;
    font-family: "Montserrat", sans-serif;
    font-size: 14px;
    color: var(--ink-soft);
  }
  .contact__item {
    display: flex;
    align-items: center;
    gap: 10px;
    margin-bottom: 7px;
  }
  .contact__icon { width: 14px; height: 14px; flex: none; }
</style>
</head>
<body>
  <main class="sheet">
    <section class="card card--front" aria-label="Card front">
      <div class="brand">
        <span class="brand__circle"></span>
        <span class="brand__name">Corvane Capital</span>
      </div>
    </section>

    <section class="card card--back" aria-label="Card back">
      <div class="brand">
        <span class="brand__circle"></span>
        <span class="brand__name">Corvane Capital</span>
      </div>
      <div class="divider"></div>
      <div class="details">
        <p class="details__company">Corvane Capital</p>
        <p class="details__name">ELIAS VARNER</p>
        <p class="details__role">Founder</p>
        <ul class="contact">
          <li class="contact__item">
            <svg class="contact__icon" viewBox="0 0 16 16" aria-hidden="true">
              <path fill="currentColor" d="M3 2h3l1.2 3.2-1.8 1.2a9 9 0 0 0 4.2 4.2l1.2-1.8L14 10v3a1 1 0 0 1-1 1A11 11 0 0 1 2 3a1 1 0 0 1 1-1z"/>
            </svg>
            <span>555-014-2290</span>
          </li>
          <li class="contact__item">
            <svg class="contact__icon" viewBox="0 0 16 16" aria-hidden="true">
              <rect x="1.5" y="3.5" width="13" height="9" fill="currentColor"/>
              <path d="M1.5 3.5 8 9l6.5-5.5" fill="none" stroke="#050505" stroke-width="1.3"/>
            </svg>
            <span>hello@corvanemail.com</span>
          </li>
        </ul>
      </div>
    </section>
  </main>
</body>
</html>
```